MRT Property - Business Cards

Looking for a business card & general letterhead, signage etc design for our new logo.

Colours:
000a20
0056a2
00b5ef
0088ce
68cef2

Fonts:
Poppins
Karla

Please keep look and feel of new brand - example in the zip package I sent.

```html
<!DOCTYPE html>
<html lang="en">
<head>
<meta charset="utf-8">
<title>MRT Property – Business Cards</title>
<link href="https://fonts.googleapis.com/css2?family=Poppins:wght@400;500;600&family=Karla:wght@400;500&display=swap" rel="stylesheet">
<style>
  :root {
    --navy-deep: #000a20;
    --navy-card: #0d1330;
    --blue-dark: #0056a2;
    --blue-mid: #0088ce;
    --blue-bright: #00b5ef;
    --blue-light: #68cef2;
    --text-light: #d9dde6;
    --white: #ffffff;
    --stage: #1f2227;
  }
  * { box-sizing: border-box; margin: 0; padding: 0; }
  html, body { width: 1200px; height: 900px; overflow: hidden; }
  body {
    background: var(--stage);
    font-family: "Karla", sans-serif;
    position: relative;
  }
  .card {
    position: absolute;
    top: 295px;
    width: 530px;
    height: 310px;
    border-radius: 26px;
    background: var(--navy-card);
    overflow: hidden;
  }
  .card--front { left: 45px; }
  .card--back { left: 625px; background: var(--navy-deep); }

  /* front */
  .edge-strip {
    position: absolute; left: 0; top: 0; bottom: 0; width: 16px;
    background: linear-gradient(to bottom, var(--blue-mid) 0 58%, var(--white) 58% 100%);
  }
  .brand {
    position: absolute;
    font-family: "Poppins", sans-serif;
    font-weight: 600;
    color: var(--white);
    display: flex; align-items: center; gap: 8px;
    letter-spacing: 0.3px;
    white-space: nowrap;
  }
  .brand__dot {
    width: 16px; height: 16px; border-radius: 50%;
    background: var(--blue-bright);
    flex: none;
  }
  .card--front .brand { left: 44px; top: 138px; font-size: 21px; }
  .divider {
    position: absolute; left: 262px; top: 62px; width: 2px; height: 186px;
    background: var(--blue-mid);
  }
  .details { position: absolute; left: 284px; top: 58px; color: var(--text-light); }
  .details__name {
    font-family: "Poppins", sans-serif; font-weight: 400;
    font-size: 26px; color: var(--blue-bright); line-height: 1.1;
  }
  .details__title { font-size: 15px; margin-top: 4px; }
  .details__address { font-size: 14px; margin-top: 10px; line-height: 1.35; }
  .contact { list-style: none; margin-top: 12px; font-size: 14px; }
  .contact li { display: flex; align-items: center; gap: 9px; line-height: 1.6; }
  .contact svg { width: 13px; height: 13px; fill: var(--blue-mid); flex: none; }

  /* back */
  .back-pattern {
    position: absolute; inset: 0;
    background: linear-gradient(160deg, #1f3a8a 0%, #14215a 30%, var(--navy-deep) 75%);
  }
  .card--back .brand { left: 50%; top: 50%; transform: translate(-50%, -50%); font-size: 30px; gap: 10px; }
  .card--back .brand__dot { width: 18px; height: 18px; }
</style>
</head>
<body>
  <section class="card card--front" aria-label="Business card front">
    <div class="edge-strip"></div>
    <div class="brand"><span class="brand__dot"></span>MRT Property</div>
    <div class="divider"></div>
    <div class="details">
      <p class="details__name">Daniel Hart</p>
      <p class="details__title">Managing Director</p>
      <p class="details__address">42 Cedar Hollow Lane<br>Brookfield, MS 39045</p>
      <ul class="contact">
        <li><svg viewBox="0 0 24 24"><path d="M6.6 10.8a15 15 0 0 0 6.6 6.6l2.2-2.2a1 1 0 0 1 1-.25 11.4 11.4 0 0 0 3.6.57 1 1 0 0 1 1 1V20a1 1 0 0 1-1 1A17 17 0 0 1 3 4a1 1 0 0 1 1-1h3.5a1 1 0 0 1 1 1c0 1.25.2 2.450 .57 3.57a1 1 0 0 1-.25 1z"/></svg>555.210.4470</li>
        <li><svg viewBox="0 0 24 24"><path d="M2 5h20v14H2zm2 2v.5l8 5 8-5V7l-8 5z"/></svg>info@mrtproperty.com</li>
        <li><svg viewBox="0 0 24 24"><path d="M12 2a10 10 0 1 0 0 20 10 10 0 0 0 0-20zm6.9 6h-3a15 15 0 0 0-1.3-3.9A8 8 0 0 1 18.9 8zM12 4a13 13 0 0 1 1.9 4h-3.8A13 13 0 0 1 12 4zM4.3 14a8 8 0 0 1 0-4h3.4a16 16 0 0 0 0 4zm.8 2h3a15 15 0 0 0 1.3 3.9A8 8 0 0 1 5.1 16zm3-8h-3a8 8 0 0 1 4.3-3.9A15 15 0 0 0 8.1 8zM12 20a13 13 0 0 1-1.9-4h3.8A13 13 0 0 1 12 20zm2.3-6H9.7a14 14 0 0 1 0-4h4.6a14 14 0 0 1 0 4zm.3 5.9a15 15 0 0 0 1.3-3.9h3a8 8 0 0 1-4.3 3.9zm1.7-5.9a16 16 0 0 0 0-4h3.4a8 8 0 0 1 0 4z"/></svg>www.mrtproperty.com</li>
      </ul>
    </div>
  </section>

  <section class="card card--back" aria-label="Business card back">
    <div class="back-pattern" role="img" aria-label="Repeating brand-symbol pattern in blue fading into navy"></div>
    <div class="brand"><span class="brand__dot"></span>MRT Property</div>
  </section>
</body>
</html>
```